Whitcombe Business Card Design

The name of the business is Dario Whitcombe, CPA LLC
The service that we offer is Accounting, Tax & Consulting Services. I need it to have the following items:
Dario Whitcombe, Principal
Phone Number
Email Address
Physical Address

I have attached the company logo, one in black and one in white. Please provide a design in black background and the other in white background. Please include "Accounting, Tax & Consulting Services". I want the business card to be clean and very professional.

```html
<!DOCTYPE html>
<html lang="en">
<head>
<meta charset="utf-8">
<title>Dario Whitcombe, CPA LLC — Business Cards</title>
<link href="https://fonts.googleapis.com/css2?family=Montserrat:wght@500;600;700&family=Roboto:wght@400&display=swap" rel="stylesheet">
<style>
  :root {
    --backdrop: #2b2b2c;
    --card-dark: #1f2022;
    --card-dark-edge: #2c2d30;
    --card-light: #f2f2f2;
    --card-light-shade: #e1e1e1;
    --brand-red: #8e1418;
    --ink: #2f3033;
    --muted: #7d7e80;
    --muted-light: #9a9b9d;
    --white: #f4f4f4;
  }
  * { margin: 0; padding: 0; box-sizing: border-box; }
  html, body {
    width: 1200px; height: 1138px; overflow: hidden;
    background: var(--backdrop);
  }
  .canvas { position: relative; width: 1200px; height: 1138px; }

  .card {
    position: absolute; left: 273px; width: 620px; height: 376px;
    border-radius: 16px; overflow: hidden;
    box-shadow: 0 6px 14px rgba(0,0,0,0.45);
  }

  /* Front: dark */
  .card--front {
    top: 184px;
    background: linear-gradient(160deg, var(--card-dark) 0%, var(--card-dark-edge) 100%);
  }
  .front-brand {
    position: absolute; left: 0; right: 0; top: 108px;
    display: flex; flex-direction: column; align-items: center;
  }
  .front-brand .brand-square {
    width: 46px; height: 46px; background: var(--brand-red); margin-bottom: 28px;
  }
  .front-brand .brand-name {
    font-family: 'Montserrat', sans-serif; font-weight: 600;
    font-size: 24.5px; letter-spacing: 0.4px; color: var(--white);
    line-height: 1;
  }
  .front-brand .brand-tagline {
    font-family: 'Montserrat', sans-serif; font-weight: 600;
    font-size: 17.5px; letter-spacing: 3px; color: var(--muted);
    margin-top: 9px; line-height: 1;
  }
  .front-brand .brand-services {
    font-family: 'Montserrat', sans-serif; font-weight: 500;
    font-size: 12px; letter-spacing: 1.6px; color: var(--muted-light);
    margin-top: 14px; line-height: 1;
  }

  /* Back: light */
  .card--back {
    top: 606px;
    background: linear-gradient(180deg, var(--card-light) 0%, var(--card-light-shade) 100%);
  }
  .back-brand { position: absolute; left: 35px; top: 54px; }
  .back-brand .brand-name {
    font-family: 'Montserrat', sans-serif; font-weight: 600;
    font-size: 19.5px; letter-spacing: 0.3px; color: var(--ink); line-height: 1;
  }
  .back-brand .brand-tagline {
    font-family: 'Montserrat', sans-serif; font-weight: 600;
    font-size: 15px; letter-spacing: 2.1px; color: var(--muted); margin-top: 6px; line-height: 1;
  }
  .back-brand .brand-services {
    font-family: 'Montserrat', sans-serif; font-weight: 500;
    font-size: 11.5px; letter-spacing: 1.3px; color: var(--muted); margin-top: 10px; line-height: 1;
  }
  .person { position: absolute; left: 35px; top: 219px; }
  .person .person-name {
    font-family: 'Montserrat', sans-serif; font-weight: 700;
    font-size: 18.5px; color: var(--brand-red); letter-spacing: 0.4px; line-height: 1;
  }
  .person .person-role {
    font-family: 'Roboto', sans-serif; font-size: 16px; color: var(--ink);
    margin-top: 6px; line-height: 1;
  }
  .contact {
    position: absolute; left: 35px; top: 300px;
    font-family: 'Roboto', sans-serif; font-size: 16.5px; color: var(--ink);
    line-height: 24px;
  }
  .contact .label { color: var(--brand-red); }
  .contact .sep { color: var(--brand-red); margin: 0 6px; }
  .back-square {
    position: absolute; left: 531px; top: 284px;
    width: 56px; height: 56px; background: var(--ink);
  }
  .footer-band {
    position: absolute; left: 0; right: 0; bottom: 0; height: 9px;
    display: flex;
  }
  .footer-band .band-red { width: 496px; background: var(--brand-red); }
  .footer-band .band-grey { flex: 1; background: var(--muted-light); }
</style>
</head>
<body>
<main class="canvas">
  <section class="card card--front" aria-label="Card front">
    <div class="front-brand">
      <span class="brand-square" aria-hidden="true"></span>
      <p class="brand-name">DARIO WHITCOMBE, CPA, LLC</p>
      <p class="brand-tagline">CERTIFIED PUBLIC ACCOUNTANT</p>
      <p class="brand-services">ACCOUNTING, TAX &amp; CONSULTING SERVICES</p>
    </div>
  </section>

  <section class="card card--back" aria-label="Card back">
    <div class="back-brand">
      <p class="brand-name">DARIO WHITCOMBE, CPA, LLC</p>
      <p class="brand-tagline">CERTIFIED PUBLIC ACCOUNTANT</p>
      <p class="brand-services">ACCOUNTING, TAX &amp; CONSULTING SERVICES</p>
    </div>
    <div class="person">
      <p class="person-name">DARIO WHITCOMBE</p>
      <p class="person-role">Principal</p>
    </div>
    <div class="contact">
      <p><span class="label">P:</span> 704-555-0192<span class="sep">|</span><span class="label">E:</span> dw@whitcombecpa.com</p>
      <p><span class="label">A:</span> 418 Linden Court, Maple Ridge, US 28803</p>
    </div>
    <span class="back-square" aria-hidden="true"></span>
    <div class="footer-band" aria-hidden="true">
      <span class="band-red"></span><span class="band-grey"></span>
    </div>
  </section>
</main>
</body>
</html>
```